Business card for a new cabinet shop company named Veloran Cabinets for high end cabinets

Design a business card, thinking dark rich green with colours to speak of high end luxury ie; cream, gold, black possibly

Mitchell Tarrowby
Director Craftsman
Email: info@veloranjoinery-example.com.au
Instagram : @veloran.cabinets

```html
<!DOCTYPE html>
<html lang="en">
<head>
<meta charset="utf-8">
<title>Veloran Cabinets – Business Card</title>
<link rel="stylesheet" href="https://fonts.googleapis.com/css2?family=Montserrat:wght@400;500;700&display=swap">
<style>
  :root {
    --backdrop: #9a9a9a;
    --card: #141414;
    --gold: #c9a85c;
    --cream: #f4f1ea;
    --silver: #d2d2d2;
  }
  * { box-sizing: border-box; margin: 0; padding: 0; }
  html, body {
    width: 1200px;
    height: 1108px;
    overflow: hidden;
    background: var(--backdrop);
    font-family: "Montserrat", sans-serif;
  }
  .card {
    position: absolute;
    left: 242px;
    width: 715px;
    height: 409px;
    border-radius: 36px;
    background: var(--card);
  }
  .card--front { top: 119px; }
  .card--back { top: 580px; }

  .front-wordmark {
    position: absolute;
    inset: 0;
    display: flex;
    align-items: center;
    justify-content: center;
    gap: 16px;
  }
  .front-wordmark .brand-square {
    width: 34px;
    height: 34px;
    border: 3px solid var(--silver);
  }
  .front-wordmark .brand-name {
    color: var(--silver);
    font-weight: 500;
    font-size: 38px;
    letter-spacing: 1px;
  }

  .back-brand {
    position: absolute;
    left: 48px;
    top: 167px;
    display: flex;
    align-items: center;
    gap: 12px;
  }
  .back-brand .brand-square {
    width: 26px;
    height: 26px;
    border: 2px solid var(--cream);
  }
  .back-brand .brand-name {
    color: var(--cream);
    font-weight: 500;
    font-size: 24px;
    letter-spacing: 0.5px;
  }

  .divider {
    position: absolute;
    left: 350px;
    top: 136px;
    width: 2px;
    height: 138px;
    background: var(--gold);
  }

  .contact {
    position: absolute;
    left: 376px;
    top: 136px;
  }
  .contact__name {
    color: var(--gold);
    font-weight: 700;
    font-size: 29px;
    line-height: 1.1;
  }
  .contact__role {
    color: var(--cream);
    font-weight: 400;
    font-size: 18px;
    margin-top: 4px;
  }
  .contact__list {
    list-style: none;
    margin-top: 30px;
  }
  .contact__item {
    display: flex;
    align-items: center;
    gap: 9px;
    color: var(--cream);
    font-size: 15.5px;
    height: 28px;
  }
  .contact__icon {
    width: 14px;
    height: 14px;
    flex: none;
  }
  .contact__icon--social {
    border: 1.6px solid var(--gold);
    border-radius: 4px;
  }
</style>
</head>
<body>
  <section class="card card--front" aria-label="Card front">
    <div class="front-wordmark">
      <span class="brand-square"></span>
      <span class="brand-name">Veloran Cabinets</span>
    </div>
  </section>

  <section class="card card--back" aria-label="Card back">
    <div class="back-brand">
      <span class="brand-square"></span>
      <span class="brand-name">Veloran Cabinets</span>
    </div>

    <div class="divider"></div>

    <div class="contact">
      <h1 class="contact__name">Mitchell Tarrowby</h1>
      <p class="contact__role">Director Craftsman</p>
      <ul class="contact__list">
        <li class="contact__item">
          <svg class="contact__icon" viewBox="0 0 14 14" aria-hidden="true">
            <rect x="0" y="3" width="14" height="9" fill="var(--gold)"/>
            <polyline points="0,3 7,8.5 14,3" fill="none" stroke="var(--card)" stroke-width="1.2"/>
          </svg>
          <span>info@veloranjoinery-example.com.au</span>
        </li>
        <li class="contact__item">
          <span class="contact__icon contact__icon--social"></span>
          <span>@veloran.cabinets</span>
        </li>
      </ul>
    </div>
  </section>
</body>
</html>
```